Vindgerdi - Start-up company selling electricity

Hello let me tell you about Vindgerdi.

Vindgerdi is start-up company selling electricity in Iceland. The operations of the company consist of making power usage forecasts for our customers, purchasing the electricity wholesale from the energy producers, and selling the electricity to the consumer. We are focused on tech by using optimization and machine learning to minimize electricity prices to our customers. Our marketing strategy is to portray a tech company mindset and to show dedication to driving down the electricity price on the market.

We need your help to make our website pop. Possible concepts to work with are as follows:

- Iceland the land of ice and fire
- Green energy
- Innovation
- Tech and data science

Link to our website: https://prufa.vindgerdi-example.is/
We are open to ideas.
Thank you!

Target Market(s)

Electricity consumers both homes and companies.

Number of Pages Required

1 page

Font styles to use
Serif
Sans Serif

```html
<!DOCTYPE html>
<html lang="en">
<head>
<meta charset="utf-8">
<title>Vindgerdi – Same electricity, just cheaper</title>
<link rel="stylesheet" href="https://fonts.googleapis.com/css2?family=Merriweather:wght@400;700&family=Open+Sans:wght@400;600;700&display=swap">
<style>
:root{
  --navy:#16305c;
  --red:#a8281f;
  --ink:#1d1d1d;
  --grey:#6a6a6a;
  --line:#d8d8d8;
  --topbar-light:#f4f4f4;
  --footer:#111214;
  --white:#ffffff;
}
*{box-sizing:border-box;margin:0;padding:0}
html,body{width:1200px;height:2656px;overflow:hidden;background:var(--white)}
body{font-family:"Open Sans",sans-serif;color:var(--ink);position:relative}
.serif{font-family:"Merriweather",serif}
.abs{position:absolute}

/* top bar */
.topbar{top:0;left:0;width:1200px;height:48px;background:var(--topbar-light)}
.topbar-contact{top:0;left:0;width:599px;height:48px;background:var(--navy);color:var(--white);font-size:15px;font-weight:600;display:flex;align-items:center;padding-left:110px;gap:14px}
.topbar-contact svg{width:13px;height:13px}
.topbar-contact .sep{margin:0 14px}
.topbar-social{top:18px;right:112px;display:flex;gap:20px}
.topbar-social span{width:12px;height:12px;border-radius:50%;background:var(--navy)}

/* nav */
.brand{display:flex;align-items:center;gap:12px}
.brand-dot{width:30px;height:30px;border-radius:50%;background:var(--red)}
.brand-name{font-family:"Merriweather",serif;font-weight:700;font-size:30px;letter-spacing:.5px;color:var(--navy)}
.header-brand{top:70px;left:112px}
.nav{top:78px;left:445px;display:flex;gap:24px;font-size:16px;font-weight:600;color:var(--ink)}
.nav .active{color:var(--red);border-bottom:2px solid var(--red);padding-bottom:6px}
.btn{display:inline-flex;align-items:center;justify-content:center;background:var(--red);color:var(--white);font-weight:700;font-size:15px;border-radius:22px;text-transform:uppercase}
.nav-cta{top:69px;left:947px;width:140px;height:42px}

/* hero */
.hero{top:129px;left:0;width:1200px;height:600px;background:radial-gradient(circle at 870px 230px,#7fd6ea 0,#2b89b4 18%,#1b4f74 40%,#13304a 70%,#0c1b2b 100%)}
.hero-title{top:345px;left:110px;font-size:27px;font-weight:700;color:var(--white)}
.hero-text{top:392px;left:111px;width:490px;font-size:17.5px;font-weight:600;line-height:28px;color:var(--white)}
.hero-cta{top:469px;left:112px;width:160px;height:42px}
.dots{top:704px;left:112px;display:flex;gap:7px}
.dots span{width:11px;height:11px;border-radius:50%;border:2px solid var(--white)}
.dots .on{background:var(--red)}

/* about */
.section-title{font-family:"Merriweather",serif;font-weight:700;font-size:27px;color:var(--ink)}
.about-title{top:855px;left:110px}
.about-body{top:904px;left:110px;width:514px;font-size:15.5px;line-height:24px;color:var(--grey);text-align:justify}
.about-body p+p{margin-top:11px}
.about-cta{top:1181px;left:111px;width:140px;height:42px}
.about-art{top:800px;left:738px;width:344px;height:500px;border-radius:170px 170px 172px 172px;background:linear-gradient(180deg,#c77f94 0%,#7a6aa8 45%,#3e6fa5 75%,#1d5f8e 100%);border:5px solid #f1f1f1}

/* future */
.future{top:1359px;left:0;width:1200px;height:416px;background:linear-gradient(100deg,#a58a52 0%,#6f6a45 30%,#4f4a38 55%,#7c8a8f 80%,#b8c4cc 100%)}
.future-panel{top:1430px;left:639px;width:411px;height:273px;background:rgba(70,64,60,.55)}
.future-title{top:1461px;left:675px;font-size:21px;font-weight:700;color:var(--white)}
.future-text{top:1500px;left:675px;width:338px;font-size:15.5px;line-height:26px;color:var(--white);text-align:justify}
.future-cta{top:1628px;left:675px;width:140px;height:42px;background:transparent;border:2px solid var(--white)}

/* faq */
.faq-title{top:1859px;left:0;width:1200px;text-align:center}
.faq-list{top:1976px;left:110px;width:455px;border:1px solid var(--line)}
.faq-item{height:47.3px;display:flex;align-items:center;justify-content:space-between;padding:0 16px;font-size:15.5px;color:#333;border-top:1px solid var(--line)}
.faq-item:first-child{border-top:none}
.faq-item svg{width:12px;height:12px}
.faq-photo{top:1936px;left:658px;width:430px;height:361px;border:6px solid #f3f3f3;box-shadow:0 0 4px rgba(0,0,0,.15);background:linear-gradient(180deg,#3a4a70 0%,#8a7a80 35%,#f0b04a 62%,#6b6a3e 80%,#2d3b44 100%)}

/* footer */
.site-footer{color:var(--white)}
.footer{top:2387px;left:0;width:1200px;height:269px;background:var(--footer)}
.footer-brand{top:2451px;left:112px}
.footer-brand .brand-name{color:var(--white);font-size:32px}
.footer-brand .brand-dot{background:var(--white)}
.footer-social{top:2511px;left:149px;display:flex;gap:13px}
.footer-social span{width:38px;height:38px;border-radius:50%;border:1.5px solid var(--white)}
.footer-col{top:2431px;font-size:16px;line-height:24px;color:var(--white)}
.footer-col h3{font-size:19px;font-weight:600;margin-bottom:12px;color:var(--white)}
.footer-col a{display:block;color:var(--white);text-decoration:none}
.col-links{left:456px}
.col-about{left:632px}
.col-contact{left:809px}
.contact-row{display:flex;align-items:center;gap:24px;color:var(--white)}
.contact-row svg{width:13px;height:13px;flex:none}
.footer-rule{top:2596px;left:110px;width:978px;height:1px;background:#5a5a5a}
.copyright{top:2610px;left:0;width:1200px;text-align:center;font-size:13px;color:var(--white)}
</style>
</head>
<body>

<div class="abs topbar"></div>
<div class="abs topbar-contact">
  <svg viewBox="0 0 16 16"><path d="M3 1l3 3-2 2c1 2 3 4 5 5l2-2 3 3-2 2C7 14 2 9 1 3z" fill="var(--red)"/></svg>
  <span>400-1234</span><span class="sep">|</span>
  <svg viewBox="0 0 16 16"><rect x="1" y="3" width="14" height="10" fill="none" stroke="var(--red)" stroke-width="1.5"/><path d="M1 3l7 6 7-6" fill="none" stroke="var(--red)" stroke-width="1.5"/></svg>
  <span>hallo@vindgerdi-example.is</span>
</div>
<div class="abs topbar-social" aria-label="Social links"><span></span><span></span><span></span><span></span></div>

<div class="abs brand header-brand"><span class="brand-dot"></span><span class="brand-name">VINDGERDI</span></div>
<nav class="abs nav">
  <span class="active">Home</span><span>About Us</span><span>Our Services</span><span>FAQ</span><span>Pricing</span><span>Blog</span>
</nav>
<a class="abs btn nav-cta">Contact Us</a>

<section>
  <div class="abs hero" role="img" aria-label="A hand reaching toward a glowing blue network globe above power lines"></div>
  <h1 class="abs hero-title serif">SAME ELECTRICITY ~ JUST CHEAPER!</h1>
  <p class="abs hero-text">Vindgerdi uses automation and artificial intelligence to achieve lower prices in the electricity market.</p>
  <a class="abs btn hero-cta">Register Now</a>
  <div class="abs dots"><span></span><span class="on"></span><span></span><span></span></div>
</section>

<section>
  <h2 class="abs section-title about-title">ABOUT VINDGERDI</h2>
  <div class="abs about-body">
    <p>Vindgerdi uses automation and artificial intelligence to achieve lower prices in the electricity market. Our goal is to minimize the cost of energy sales, promote energy balance and offer good service.</p>
    <p>Vindgerdi's goal is to offer its customers the most favorable electricity prices in Iceland. Electricity is part of the monthly costs of households and companies, and by doing business with Vindgerdi, savings can be achieved and operating costs reduced. Vindgerdi wants to make the electricity system "smarter". Data science and the use of artificial intelligence can maximize the efficiency of the electricity system, minimize electricity costs and promote energy balance.</p>
  </div>
  <a class="abs btn about-cta">Read More</a>
  <div class="abs about-art" role="img" aria-label="Electricity pylons under a dusky purple and blue sky with network points"></div>
</section>

<section>
  <div class="abs future" role="img" aria-label="Aerial view of an Icelandic mountain landscape with a winding road along a fjord at sunset"></div>
  <div class="abs future-panel"></div>
  <h2 class="abs future-title serif">THE FUTURE IS EXCITING</h2>
  <p class="abs future-text">Let's make the electricity system smarter together. Vindgerdi uses artificial intelligence, data science and automation to minimize costs and promote eccentricity</p>
  <a class="abs btn future-cta">Read More</a>
</section>

<section>
  <h2 class="abs section-title faq-title">FREQUENTLY ASKED QUESTIONS</h2>
  <div class="abs faq-list">
    <div class="faq-item">Can anyone buy electricity from Vindgerdi?<svg viewBox="0 0 12 12"><path d="M6 1v10M1 6h10" stroke="#444" stroke-width="2.2"/></svg></div>
    <div class="faq-item">How do I buy electricity from Vindgerdi?<svg viewBox="0 0 12 12"><path d="M6 1v10M1 6h10" stroke="#444" stroke-width="2.2"/></svg></div>
    <div class="faq-item">Does it cost to switch to Vindgerdi?<svg viewBox="0 0 12 12"><path d="M6 1v10M1 6h10" stroke="#444" stroke-width="2.2"/></svg></div>
    <div class="faq-item">What happens after I sign up for a business?<svg viewBox="0 0 12 12"><path d="M6 1v10M1 6h10" stroke="#444" stroke-width="2.2"/></svg></div>
    <div class="faq-item">The Future with Vindgerdi?<svg viewBox="0 0 12 12"><path d="M6 1v10M1 6h10" stroke="#444" stroke-width="2.2"/></svg></div>
    <div class="faq-item">How do I quit trading?<svg viewBox="0 0 12 12"><path d="M6 1v10M1 6h10" stroke="#444" stroke-width="2.2"/></svg></div>
  </div>
  <div class="abs faq-photo" role="img" aria-label="Power pylon, wind turbines and solar panels under a golden sunset sky"></div>
</section>

<footer class="site-footer">
  <div class="abs footer"></div>
  <div class="abs brand footer-brand"><span class="brand-dot"></span><span class="brand-name">VINDGERDI</span></div>
  <div class="abs footer-social" aria-label="Social links"><span></span><span></span><span></span><span></span></div>
  <div class="abs footer-col col-links"><h3>Quick Links</h3><a>Home</a><a>About Us</a><a>Our Services</a><a>Pricing</a></div>
  <div class="abs footer-col col-about"><h3>About</h3><a>Site Map</a><a>Privacy Policy</a><a>Terms of Use</a></div>
  <div class="abs footer-col col-contact"><h3>Contact Us</h3>
    <div class="contact-row"><svg viewBox="0 0 16 16"><path d="M8 1a5 5 0 0 0-5 5c0 4 5 9 5 9s5-5 5-9a5 5 0 0 0-5-5z" fill="var(--red)"/><circle cx="8" cy="6" r="2" fill="var(--footer)"/></svg><span>Vindvegur 4 170 Fjardarbaer</span></div>
    <div class="contact-row"><svg viewBox="0 0 16 16"><rect x="1" y="3" width="14" height="10" fill="none" stroke="var(--red)" stroke-width="1.5"/><path d="M1 3l7 6 7-6" fill="none" stroke="var(--red)" stroke-width="1.5"/></svg><span>hallo@vindgerdi-example.is</span></div>
    <div class="contact-row"><svg viewBox="0 0 16 16"><path d="M3 1l3 3-2 2c1 2 3 4 5 5l2-2 3 3-2 2C7 14 2 9 1 3z" fill="var(--red)"/></svg><span>400-1234</span></div>
  </div>
  <div class="abs footer-rule"></div>
  <p class="abs copyright">© Copyrights 2021 VINDGERDI. All rights reserved</p>
</footer>

</body>
</html>
```